PDF flyer for our companies' two main products: Food processing machines.

PDF flyer with showcasing two products. Flyer can be one page per product, or both products on the same page.

Product #1: Labeled "Ribbon blenders".
Showing a photo of the machine, and the details/features offered with that machine. Product description must also say: "Sizes available; 2 Cu Ft. - 450 Cu Ft."

Product #2: Labeled: " Auger hoppers / Screw feeders"
Showing a photo of the machine, and the details/features offered with that machine.

SEE UPLOADED IMAGES; "Ribbon Blenders EXAMPLE FLYER".
& "Auger Hoppers / Screw Conveyors EXAMPLE FLYER" for a rough idea of what we are looking for.

Target Market(s)

Copackers, Packing houses, Food manufacturers, protein powder producers,

Industry/Entity Type

Commercial Food processing / packing / mixing equipment

Font styles to use
Serif

Colors
0054AA
0677BA
7BADD7
CADEEF
E8F1F8

Requirements
Must have
• Company logo on top of flyer.
Nice to have
• I would like for the flyer to show some stock images of common ingredients, similar to the images uploaded.
Should not have
• Pictures with background. Backgrounds must be removed from provides photos. "clipping path"

```html
<!DOCTYPE html>
<html lang="en">
<head>
<meta charset="utf-8">
<title>Steelbrook Ribbon Blenders and Auger Hopper Flyer</title>
<link href="https://fonts.googleapis.com/css2?family=Michroma&family=Tinos:wght@400;700&family=Carlito:wght@400;700&display=swap" rel="stylesheet">
<style>
  :root{
    --blue-deep:#0054AA;
    --blue-mid:#0677BA;
    --blue-soft:#7BADD7;
    --blue-pale:#CADEEF;
    --blue-mist:#E8F1F8;
    --ink:#1b1b1b;
    --band-dark:#2c2c2e;
    --paper:#ffffff;
    --stage:#d9dadc;
  }
  *{box-sizing:border-box;margin:0;padding:0}
  html,body{width:1200px;height:675px;overflow:hidden;background:var(--stage)}
  body{position:relative;font-family:"Tinos",serif;color:var(--ink)}
  .page{position:absolute;top:22px;width:460px;height:630px;background:var(--paper);overflow:hidden;box-shadow:0 4px 14px rgba(0,0,0,.18)}
  .page--blender{left:110px}
  .page--auger{left:630px}
  .hero{position:absolute;left:0;top:0;width:460px;background:linear-gradient(135deg,var(--blue-deep),var(--blue-mid))}
  .page--blender .hero{height:300px;clip-path:polygon(0 0,100% 0,100% 100%,0 72%)}
  .page--auger .hero{height:335px;clip-path:polygon(0 0,100% 0,100% 100%,0 66%)}
  .brand{position:absolute;display:flex;align-items:center;gap:5px;font-family:"Michroma",sans-serif;font-size:9px;color:#fff;letter-spacing:.5px}
  .brand__dot{width:9px;height:9px;border-radius:50%;background:#fff}
  .page--blender .brand{right:18px;top:12px}
  .page--auger .brand{right:18px;top:80px}
  .title{position:absolute;font-family:"Michroma",sans-serif;color:#fff;line-height:1.1}
  .page--blender .title{left:22px;top:36px;font-size:22px}
  .page--auger .title{right:18px;top:98px;font-size:19px;text-align:right}
  .subhead{position:absolute;font-family:"Michroma",sans-serif;color:#fff;font-size:10px}
  .page--blender .subhead{left:22px;top:68px}
  .page--auger .subhead{right:18px;top:206px}
  .features{position:absolute;list-style:none;color:#fff;font-size:8px;line-height:1.35}
  .page--blender .features{left:22px;top:86px;width:260px}
  .page--auger .features{right:18px;top:222px;width:200px}
  .features li,.options li{position:relative;padding-left:11px;margin-bottom:2px}
  .features li::before,.options li::before{content:"";position:absolute;left:0;top:2px;width:6px;height:6px;border-radius:50%;background:#fff}
  .options li::before{background:var(--blue-deep)}
  .photo{position:absolute;border-radius:4px}
  .photo--blender{left:285px;top:100px;width:165px;height:175px;background:linear-gradient(160deg,#e4e6e8,#9a9ea3 60%,#6f7377)}
  .photo--auger{left:10px;top:128px;width:195px;height:88px;background:linear-gradient(160deg,#e6e8ea,#a1a5aa 60%,#74787c)}
  .photo--spoons{left:310px;top:338px;width:145px;height:110px;border-radius:10px;background:linear-gradient(160deg,#e9b23a,#c79a35 45%,#d2542c)}
  .size-band{position:absolute;left:0;top:182px;width:300px;height:26px;background:var(--band-dark);clip-path:polygon(0 0,100% 0,93% 100%,0 100%);color:#fff;font-family:"Michroma",sans-serif;font-size:11px;display:flex;align-items:center;justify-content:space-between;padding:0 30px 0 14px}
  .spice{position:absolute;width:62px;height:62px;border-radius:50%;border:3px solid var(--blue-mid);background:radial-gradient(circle at 40% 40%,#e07a22,#8a3b14 70%,#3a1a0c)}
  .spice--green{background:radial-gradient(circle at 40% 40%,#a9b35a,#6c7a33 60%,#c2561f)}
  .spice--bark{background:radial-gradient(circle at 40% 40%,#d1a06a,#8e5a2c 65%,#4a2b15)}
  .spice--pepper{background:radial-gradient(circle at 40% 40%,#c9b39a,#5a4a3c 65%,#2a221c)}
  .option-head{position:absolute;font-family:"Michroma",sans-serif;font-size:10px;color:var(--blue-deep)}
  .options{position:absolute;list-style:none;font-size:8px;line-height:1.35}
  .page--blender .option-head{left:22px;top:300px}
  .page--blender .options{left:22px;top:316px;width:300px}
  .page--auger .option-head{left:22px;top:340px}
  .page--auger .options{left:22px;top:356px;width:280px}
  .spec{position:absolute;border-collapse:collapse;font-family:"Carlito",sans-serif;background:var(--paper)}
  .spec td,.spec th{border:1px solid #555;padding:1px 3px;text-align:left;font-weight:400}
  .spec th{font-weight:700}
  .spec sup{font-size:70%;line-height:0}
  .spec--blender{left:22px;top:388px;width:416px;font-size:6.4px}
  .spec--blender td,.spec--blender th{border-color:#bbb}
  .spec--auger{left:22px;top:458px;width:420px;font-size:8px}
  .spec--auger td,.spec--auger th{border-width:1.5px;border-color:#111}
  .contact{position:absolute;bottom:0;left:0;height:40px;background:var(--blue-deep);color:#fff;font-family:"Michroma",sans-serif;font-size:11px;display:flex;align-items:center;gap:8px;padding-left:40px}
  .page--blender .contact{width:460px;clip-path:polygon(8% 0,100% 0,100% 100%,0 100%)}
  .page--auger .contact{width:330px;clip-path:polygon(0 0,88% 0,100% 100%,0 100%);padding-left:20px}
  .contact svg{width:12px;height:12px;fill:#fff}
</style>
</head>
<body>

<section class="page page--blender">
  <div class="hero"></div>
  <div class="brand"><span class="brand__dot"></span>STEELBROOK</div>
  <h1 class="title">RIBBON BLENDERS</h1>
  <h2 class="subhead">STANDARD FEATURES:</h2>
  <ul class="features">
    <li>Pre-wired control panels with; batch timer, on/off switch, emergency stop button</li>
    <li>304 stainless steel construction, Food grade compression shaft seals.</li>
    <li>Safety sensor on lid for automatic shutoff when opened.</li>
    <li>Air actuated discharge valve, 1 piece hinged lid with safety grating.</li>
    <li>Power options; 220v/480v, 24" standard discharge height.</li>
    <li>Castor wheels on 53cf units and smaller.</li>
  </ul>
  <div class="photo photo--blender" role="img" aria-label="Stainless steel ribbon blender on a wheeled frame with control panel"></div>
  <div class="size-band"><span>2 CU FT - 450 CU FT</span><span>SIZE</span></div>

  <div class="spice" style="left:150px;top:214px" role="img" aria-label="Spoons of colourful ground spices"></div>
  <div class="spice spice--bark" style="left:210px;top:232px" role="img" aria-label="Bowl of chili flakes and peppercorns"></div>
  <div class="spice" style="left:270px;top:250px" role="img" aria-label="Bowls of turmeric and curry powder"></div>
  <div class="spice spice--green" style="left:330px;top:268px" role="img" aria-label="Dried herbs and paprika"></div>
  <div class="spice" style="left:390px;top:286px" role="img" aria-label="Assorted spices on spoons"></div>

  <h3 class="option-head">OPTION:</h3>
  <ul class="options">
    <li>Dual hinged lids available on custom orders. Knife gate style discharge available on custom orders.</li>
    <li>Air purge seals available on custom orders. 316 stainless material available on custom orders.</li>
    <li>Custom height modification. Liquid spray systems - (VFD) Variable Frequency Drives - Leg extensions</li>
  </ul>

  <table class="spec spec--blender">
    <tr><th>Model Size</th><th>5cf</th><th>7CF</th><th>10.5CF</th><th>17.5CF</th><th>35CF</th><th>53CF</th><th>70.5CF</th><th>106CF</th></tr>
    <tr><td>Working Liters</td><td>120L</td><td>200L</td><td>300L</td><td>500L</td><td>1000L</td><td>1500L</td><td>2000L</td><td>3000L</td></tr>
    <tr><td>Fill Capacity</td><td>5CF/150L</td><td>9CF/250L</td><td>13CF/375L</td><td>22CF/625L</td><td>44CF/1250L</td><td>66CF/1875L</td><td>88CF/2500L</td><td>132CF/3750L</td></tr>
    <tr><td>Weight</td><td>440lbs</td><td>660lbs</td><td>770lbs</td><td>1212lbs</td><td>1874lbs</td><td>2645lbs</td><td>3527lbs</td><td>5511lbs</td></tr>
    <tr><td>Motor Size</td><td>4hp</td><td>5.5hp</td><td>6.7hp</td><td>10hp</td><td>14.75hp</td><td>20hp</td><td>25hp</td><td>30hp</td></tr>
    <tr><td>Total Length</td><td>50"</td><td>53.5"</td><td>63"</td><td>72"</td><td>94"</td><td>102"</td><td>131.5"</td><td>157.5"</td></tr>
    <tr><td>Total Width</td><td>25"</td><td>34"</td><td>41.5"</td><td>45"</td><td>52"</td><td>66"</td><td>52.5"</td><td>54"</td></tr>
    <tr><td>Total Height</td><td>66"</td><td>69"</td><td>71"</td><td>82"</td><td>87"</td><td>95"</td><td>76"</td><td>110"</td></tr>
    <tr><td>Tub Length</td><td>31.5"</td><td>35.5"</td><td>41"</td><td>47.5"</td><td>59"</td><td>70"</td><td>75"</td><td>100"</td></tr>
    <tr><td>Tub Width</td><td>16.5"</td><td>20"</td><td>25"</td><td>35.5"</td><td>39"</td><td>46"</td><td>48"</td><td>48"</td></tr>
    <tr><td>Shaft Diameter</td><td>20.5"</td><td>26"</td><td>28"</td><td>41"</td><td>46"</td><td>51"</td><td>53"</td><td>53"</td></tr>
    <tr><td>Tub Thickness</td><td>2"</td><td>2-1/4"</td><td>2-3/8"</td><td>3"</td><td>3.5"</td><td>4"</td><td>4"</td><td>5-1/4"</td></tr>
    <tr><td>Ribbon Thickness</td><td>3mm</td><td>3mm</td><td>3mm</td><td>4mm</td><td>4mm</td><td>5mm</td><td>6mm</td><td>6mm</td></tr>
    <tr><td>Max RPM</td><td>46rpm</td><td>46rpm</td><td>46rpm</td><td>46rpm</td><td>30rpm</td><td>31rpm</td><td>32rpm</td><td>33rpm</td></tr>
  </table>

  <div class="contact">
    <svg viewBox="0 0 24 24" aria-hidden="true"><path d="M6.6 10.8a15 15 0 0 0 6.6 6.6l2.2-2.2c.3-.3.7-.4 1-.2 1.1.4 2.3.6 3.6.6.6 0 1 .4 1 1V20c0 .6-.4 1-1 1C10.6 21 3 13.4 3 4c0-.6.4-1 1-1h3.5c.6 0 1 .4 1 1 0 1.3.2 2.5.6 3.6.1.3 0 .7-.2 1z"/></svg>
    CONTACT US: +1 555 010 0199
  </div>
</section>

<section class="page page--auger">
  <div class="hero"></div>
  <div class="spice" style="left:20px;top:16px" role="img" aria-label="Turmeric root and ground turmeric"></div>
  <div class="spice spice--bark" style="left:120px;top:40px" role="img" aria-label="Cinnamon sticks tied with string"></div>
  <div class="spice spice--pepper" style="left:215px;top:88px" role="img" aria-label="Black pepper in wooden spoons"></div>
  <div class="photo photo--auger" role="img" aria-label="Stainless steel auger hopper with inclined screw conveyor tube"></div>
  <div class="spice spice--bark" style="left:12px;top:226px" role="img" aria-label="Ground spice in a bowl with star anise"></div>
  <div class="spice spice--bark" style="left:90px;top:246px" role="img" aria-label="Wooden bowl of ground cumin"></div>
  <div class="spice spice--green" style="left:168px;top:232px" role="img" aria-label="Jar of dried herbs"></div>

  <div class="brand"><span class="brand__dot"></span>STEELBROOK</div>
  <h1 class="title">AUGER<br>HOPPER /<br>SCREW<br>CONVEYOR</h1>
  <h2 class="subhead">STANDARD FEATURES:</h2>
  <ul class="features">
    <li>Direct Drive. - 304 Stainless steel construction, Stainless steel safety grating</li>
    <li>Pre-wired control panel. - Electric Vibrator. - Castor Wheels.</li>
  </ul>

  <div class="photo photo--spoons" role="img" aria-label="Spoons of turmeric, curry and paprika powder"></div>

  <h3 class="option-head">OPTION:</h3>
  <ul class="options">
    <li>Square or round hopper. 3.5cf and 7cf hoppers are standard, Custom hoppers up to 200cf. - VFD (Variable Frequency Drive)</li>
    <li>Clamshell Auger tube for easy cleanout</li>
    <li>316 Stainless steel construction.</li>
  </ul>

  <table class="spec spec--auger">
    <tr><th>MODEL</th><th>AH-A2</th><th>AH-A3</th><th>AH-A5</th><th>AH-A7</th><th>AH-A8</th><th>AH-A12</th></tr>
    <tr><td>FEEDING RATE</td><td>2m<sup>3</sup>/hr</td><td>3m<sup>3</sup>/hr</td><td>5m<sup>3</sup>/hr</td><td>7m<sup>3</sup>/hr</td><td>8m<sup>3</sup>/hr</td><td>12m<sup>3</sup>/hr</td></tr>
    <tr><td>PIPE DIAMETER</td><td>4"</td><td>4-1/2"</td><td>5-1/2"</td><td>6-1/4"</td><td>6-1/2"</td><td>8-1/2"</td></tr>
    <tr><td>HOPPER VOL.</td><td>3.5CF</td><td colspan="5">7CF</td></tr>
    <tr><td>DIMENSIONS</td><td>28.6"x24.4"x31.5"</td><td colspan="5">40" x 32" x 35"</td></tr>
    <tr><td>TOTAL WEIGHT</td><td>221LBS</td><td>287LBS</td><td>397LBS</td><td>441LBS</td><td>485LBS</td><td>596LBS</td></tr>
    <tr><td>CHARGING HEIGHT</td><td colspan="6">STANDARD 72 INCHES. (40" - 196" AVAILABLE)</td></tr>
    <tr><td>CHARGING ANGLE</td><td colspan="6">STANDARD 45° (30°-60° AVAILABLE)</td></tr>
  </table>

  <div class="contact">
    <svg viewBox="0 0 24 24" aria-hidden="true"><path d="M2 5h20v14H2z M2 5l10 8 10-8" stroke="#0054AA" stroke-width="1.5"/></svg>
    MAIL US: INFO@STEELBROOK.COM
  </div>
</section>

</body>
</html>
```